Small Business Broker Business Card Design

A business card design for a small business brokerage, which is a financial service, not unlike real estate brokerage, but for small businesses such as laundromats, pizza shops, restaurants, cleaners etc. The designs should all be simple, more conservative in nature, using the colors and font of the logo. Again, think real estate Brokerage as a business context
Contact Information for Business Card
Name: Glen R. Harlow. Title: Small Business Advisor. Email: g.harlow@bayfieldcapitalworks.example. Mobile: (555) 274-3918. Office: (555) 806-2147. www.bayfieldcapitalworks.example

```html
<!DOCTYPE html>
<html lang="en">
<head>
<meta charset="utf-8">
<title>Bayfield Capital Works – Business Card</title>
<link rel="stylesheet" href="https://fonts.googleapis.com/css2?family=Montserrat:wght@600;800&family=Arimo:wght@400;700&display=swap">
<style>
  :root {
    --page-bg: #1b1d22;
    --navy: #17305f;
    --navy-deep: #132a55;
    --navy-light: #1d3a6d;
    --green: #8cc63f;
    --white: #ffffff;
    --card-w: 660px;
    --card-h: 377px;
  }
  * { margin: 0; padding: 0; box-sizing: border-box; }
  html, body {
    width: 1200px; height: 963px; overflow: hidden;
    background: var(--page-bg);
  }
  .stage {
    position: relative; width: 1200px; height: 963px;
    display: flex; flex-direction: column; align-items: center; justify-content: center; gap: 50px;
  }
  .card {
    position: relative; width: var(--card-w); height: var(--card-h);
    border-radius: 22px; overflow: hidden;
    background: radial-gradient(ellipse at 40% 45%, var(--navy-light), var(--navy) 55%, var(--navy-deep));
    color: var(--white);
    font-family: "Arimo", Arial, sans-serif;
  }
  /* Front */
  .contact-name {
    position: absolute; left: 40px; top: 62px;
    font-weight: 700; font-size: 30px; line-height: 34px;
    color: var(--green);
  }
  .contact-title {
    position: absolute; left: 40px; top: 101px;
    font-size: 17px; color: var(--white);
  }
  .divider {
    position: absolute; left: 36px; right: 60px; top: 136px;
    height: 1px; background: var(--white);
  }
  .phones { position: absolute; left: 40px; top: 152px; list-style: none; }
  .phones li {
    display: flex; align-items: center; gap: 10px;
    font-size: 17px; line-height: 30px;
  }
  .phones svg { width: 16px; height: 16px; flex: none; }
  .brand {
    position: absolute; right: 40px; top: 34px; text-align: right;
  }
  .brand-mark {
    display: inline-block; width: 34px; height: 34px; background: var(--green);
    margin-bottom: 10px;
  }
  .brand-name {
    font-family: "Montserrat", Arial, sans-serif; font-weight: 800;
    font-size: 17px; letter-spacing: 0.5px; text-transform: uppercase; color: var(--white);
  }
  .brand-tagline {
    font-family: "Montserrat", Arial, sans-serif; font-weight: 600;
    font-size: 8.6px; letter-spacing: 1px; text-transform: uppercase; color: var(--green);
    margin-top: 3px;
  }
  .email {
    position: absolute; right: 60px; top: 246px;
    display: flex; align-items: center; gap: 10px; font-size: 17px;
  }
  .email svg { width: 17px; height: 13px; }
  .bottom-bands { position: absolute; left: 0; bottom: 0; width: 660px; height: 90px; }
  .website {
    position: absolute; right: 36px; bottom: 12px;
    font-size: 18px; color: var(--white);
  }
  /* Back */
  .back .brand { top: 48px; }
  .back .brand-name { font-size: 22px; }
  .back .brand-tagline { font-size: 11px; }
</style>
</head>
<body>
<main class="stage">
  <section class="card front" aria-label="Business card front">
    <h1 class="contact-name">Glen R. Harlow</h1>
    <p class="contact-title">Small Business Advisor</p>
    <div class="divider"></div>
    <ul class="phones">
      <li>
        <svg viewBox="0 0 16 16" aria-hidden="true"><path d="M3 1.5l2.5 0 1.2 3-1.6 1.2a8 8 0 0 0 4.2 4.2l1.2-1.6 3 1.2v2.5a1.5 1.5 0 0 1-1.6 1.5A12 12 0 0 1 1.5 3.1 1.5 1.5 0 0 1 3 1.5z" fill="none" stroke="#8cc63f" stroke-width="1.4"/></svg>
        (555) 806-2147
      </li>
      <li>
        <svg viewBox="0 0 16 16" aria-hidden="true"><rect x="4" y="1" width="8" height="14" rx="1.5" fill="none" stroke="#8cc63f" stroke-width="1.4"/><line x1="7" y1="12.5" x2="9" y2="12.5" stroke="#8cc63f" stroke-width="1.4"/></svg>
        (555) 274-3918
      </li>
    </ul>
    <div class="brand">
      <span class="brand-mark" aria-hidden="true"></span>
      <p class="brand-name">Bayfield Capital Works, Inc</p>
      <p class="brand-tagline">Trusted guidance for every main street sale</p>
    </div>
    <p class="email">
      <svg viewBox="0 0 17 13" aria-hidden="true"><rect x="0.7" y="0.7" width="15.6" height="11.6" fill="none" stroke="#8cc63f" stroke-width="1.4"/><path d="M0.7 0.7l7.8 6.5 7.8-6.5" fill="none" stroke="#8cc63f" stroke-width="1.4"/></svg>
      g.harlow@bayfieldcapitalworks.example
    </p>
    <svg class="bottom-bands" viewBox="0 0 660 90" preserveAspectRatio="none" aria-hidden="true">
      <polygon points="0,0 260,48 260,90 0,90" fill="#ffffff"/>
      <polygon points="210,90 262,42 660,42 660,90" fill="#8cc63f"/>
    </svg>
    <p class="website">www.bayfieldcapitalworks.example</p>
  </section>

  <section class="card back" aria-label="Business card back">
    <div class="brand">
      <p class="brand-name">Bayfield Capital Works, Inc</p>
      <p class="brand-tagline">Trusted guidance for every main street sale</p>
    </div>
  </section>
</main>
</body>
</html>
```